Tolvik Commercial Cleaning is lookong for a new business card design.

A fresh new design that's professional and stylish. We need a serious upgrade to our business cards. I have included pictures of our existing ones. Our clients include professional individuals and business owners. We woupdblike something professional and upbeat. Please have fun and see what you come uo with.

Target Market(s)

Property managers, business owners, facility managers and other similar professionals

Industry/Entity Type

Janitorial

Contact Information for Business Card

Name, cell, office number, email, web address

Font styles to use
Sans Serif

Colors

Designer to choose colors to be used in the design.

Requirements
Must have
• please use the green color in our logo
Nice to have
• Bar code
Should not have
• Address

```html
<!DOCTYPE html>
<html lang="en">
<head>
<meta charset="UTF-8">
<title>Tolvik Commercial Cleaning – Business Card</title>
<link rel="stylesheet" href="https://fonts.googleapis.com/css2?family=Open+Sans:wght@400;700&display=swap">
<style>
  :root {
    --backdrop: #ecebe8;
    --brand-green: #3bb65a;
    --deep-green: #2a8c43;
    --card-dark: #1f2025;
    --accent-blue: #3f72b5;
    --text-light: #f2f2f2;
    --divider: #8a8c92;
  }
  * { margin: 0; padding: 0; box-sizing: border-box; }
  html, body {
    width: 1200px;
    height: 780px;
    overflow: hidden;
    background: var(--backdrop);
    font-family: "Open Sans", Arial, sans-serif;
  }
  .sheet {
    position: relative;
    width: 1200px;
    height: 780px;
  }
  .card {
    position: absolute;
    width: 560px;
    height: 320px;
    border-radius: 4px;
    box-shadow: 0 6px 18px rgba(0,0,0,0.22);
  }
  .card--front {
    left: 170px;
    top: 50px;
    background: var(--brand-green);
    display: flex;
    align-items: center;
    justify-content: center;
  }
  .card--back {
    left: 470px;
    top: 410px;
    background: var(--card-dark);
  }
  .brand {
    display: flex;
    align-items: center;
    gap: 14px;
  }
  .brand__dot {
    width: 22px;
    height: 22px;
    border-radius: 50%;
    background: currentColor;
  }
  .brand__name {
    font-weight: 700;
    letter-spacing: 1px;
    line-height: 1;
  }
  .card--front .brand { color: var(--deep-green); }
  .card--front .brand__name { font-size: 64px; }
  .brand__tag {
    margin-top: 10px;
    font-size: 17px;
    font-weight: 700;
    letter-spacing: 1px;
    text-align: center;
    color: var(--deep-green);
  }
  .back__logo {
    position: absolute;
    left: 40px;
    top: 0;
    width: 230px;
    height: 100%;
    display: flex;
    flex-direction: column;
    justify-content: center;
  }
  .card--back .brand { color: var(--brand-green); }
  .card--back .brand__name { font-size: 44px; }
  .card--back .brand__dot { width: 16px; height: 16px; }
  .back__tag {
    margin-top: 8px;
    font-size: 13px;
    font-weight: 700;
    letter-spacing: 0.5px;
    color: var(--accent-blue);
  }
  .back__divider {
    position: absolute;
    left: 292px;
    top: 70px;
    width: 1px;
    height: 180px;
    background: var(--divider);
  }
  .contact {
    position: absolute;
    left: 318px;
    top: 88px;
  }
  .contact__name {
    font-size: 25px;
    font-weight: 700;
    margin-bottom: 22px;
    white-space: nowrap;
  }
  .contact__first { color: var(--brand-green); }
  .contact__last { color: var(--accent-blue); }
  .contact__list { list-style: none; }
  .contact__item {
    display: flex;
    align-items: center;
    gap: 10px;
    font-size: 13.5px;
    color: var(--text-light);
    margin-bottom: 9px;
    white-space: nowrap;
  }
  .contact__icon {
    width: 15px;
    height: 15px;
    flex: none;
  }
</style>
</head>
<body>
<main class="sheet">
  <section class="card card--front" aria-label="Card front">
    <div>
      <div class="brand">
        <span class="brand__dot"></span>
        <span class="brand__name">Tolvik</span>
      </div>
      <p class="brand__tag">commercial cleaning</p>
    </div>
  </section>

  <section class="card card--back" aria-label="Card back">
    <div class="back__logo">
      <div class="brand">
        <span class="brand__dot"></span>
        <span class="brand__name">Tolvik</span>
      </div>
      <p class="back__tag">commercial cleaning</p>
    </div>

    <div class="back__divider"></div>

    <div class="contact">
      <h1 class="contact__name"><span class="contact__first">Dana</span> <span class="contact__last">Whitfield</span></h1>
      <ul class="contact__list">
        <li class="contact__item">
          <svg class="contact__icon" viewBox="0 0 24 24" aria-hidden="true"><path fill="#3bb65a" d="M6.6 10.8a15.1 15.1 0 0 0 6.6 6.6l2.2-2.2c.3-.3.7-.4 1-.2 1.1.4 2.3.6 3.6.6.6 0 1 .4 1 1V20c0 .6-.4 1-1 1A17 17 0 0 1 3 4c0-.6.4-1 1-1h3.5c.6 0 1 .4 1 1 0 1.3.2 2.5.6 3.6.1.3 0 .7-.2 1z"/></svg>
          (555) 014-2270
        </li>
        <li class="contact__item">
          <svg class="contact__icon" viewBox="0 0 24 24" aria-hidden="true"><rect x="2" y="5" width="20" height="14" rx="2" fill="#3bb65a"/><path d="M3 6l9 7 9-7" fill="none" stroke="#1f2025" stroke-width="1.8"/></svg>
          dana@tolvikcleaning.com
        </li>
        <li class="contact__item">
          <svg class="contact__icon" viewBox="0 0 24 24" aria-hidden="true"><circle cx="12" cy="12" r="10" fill="#3bb65a"/><path d="M2 12h20M12 2c3 3 3 17 0 20M12 2c-3 3-3 17 0 20" fill="none" stroke="#1f2025" stroke-width="1.4"/></svg>
          www.tolvikcleaning.com
        </li>
      </ul>
    </div>
  </section>
</main>
</body>
</html>
```